I need a complete stationary pack for a real estate office that sells and manages residential proper

We need a stationary design pack for my real estate office called ‘brightkeyhomes’ that is in Queensland Australia. My offices are both in suburban and coastal locations in the south west corner of Queensland at the Coral Bay Shore and Brisbane.
We predominately manage real estate on behalf of owners and sell property in the residential sector.
I have attached a copy of our existing design of my business card and do like the current concept/layout. In saying this you may be able to use this existing theme across to the other items required or see opportunity on how to improve what I have already.
I would like to see concepts for the following products:
- Letterhead
- Fax header
- Business cards
- Email signature
- With complements slips and
- Envelopes
I have attached our current logo that was designed by Artfolder and the font is Prelo.

I am looking for a contemporary design that is professional and reflects trust and professionalism. I am currently using the logo with a black background on some material as per the following link

http://www.plotlisting.com.au/property/for-sale/house/qld/merridale/?adid=4827305118&sp=7

I have posted another job 517362 for signage and the company car signage done too if you are interested.

Please do not hesitate to contact me should you have any questions. Thank you.

Target Market(s)

Western speaking people aged from 25 to 60 from modest backgrounds to well off individuals

Industry/Entity Type

Real Estate

Requirements
Must have
• Professional in appearance, show a mature and trustworthy image
Should not have
• As there is good colour with the logo, i am do not want over the top designs or colours

```html
<!DOCTYPE html>
<html lang="en">
<head>
<meta charset="utf-8">
<title>brightkeyhomes stationery pack</title>
<link rel="stylesheet" href="https://fonts.googleapis.com/css2?family=Open+Sans:ital,wght@0,400;0,600;1,400&display=swap">
<style>
  :root {
    --backdrop: #ece8e2;
    --paper: #ffffff;
    --ink: #2d313b;
    --ink-soft: #555a66;
    --black: #060606;
    --red: #d42a2c;
    --purple: #6b2a83;
    --blue: #1f78c1;
    --green: #2e9c47;
    --orange: #f29a1e;
    --flame: #e2532a;
    --flap-blue: #1b73bb;
    --flap-green: #2c9b4a;
    --flap-red: #d3262b;
  }
  * { box-sizing: border-box; margin: 0; padding: 0; }
  html, body { width: 1200px; height: 900px; overflow: hidden; }
  body {
    position: relative;
    background: var(--backdrop);
    font-family: "Open Sans", Arial, sans-serif;
    color: var(--ink);
  }
  .sheet { position: absolute; background: var(--paper); box-shadow: 0 1px 3px rgba(0,0,0,.12); }

  .wordmark { display: flex; align-items: center; gap: 6px; font-weight: 600; color: var(--ink); white-space: nowrap; }
  .wordmark .dot { border-radius: 50%; background: var(--red); flex: none; }
  .wordmark--light { color: #ffffff; }

  .colour-bar { position: absolute; display: flex; justify-content: space-between; }
  .colour-bar span { display: block; height: 100%; }
  .colour-bar span:nth-child(1) { background: var(--red); }
  .colour-bar span:nth-child(2) { background: var(--purple); }
  .colour-bar span:nth-child(3) { background: var(--blue); }
  .colour-bar span:nth-child(4) { background: var(--green); }
  .colour-bar span:nth-child(5) { background: var(--orange); }
  .colour-bar span:nth-child(6) { background: var(--flame); }

  .contact { position: absolute; display: flex; color: var(--ink-soft); }
  .contact__col { padding: 0 10px; border-left: 1px solid #c9cbd1; }
  .contact__col:first-child { padding-left: 0; border-left: none; }
  .contact .label { color: var(--red); }

  /* Letterhead */
  .letterhead { left: 24px; top: 36px; width: 333px; height: 471px; }
  .letterhead .wordmark { position: absolute; right: 34px; top: 50px; font-size: 14px; }
  .letterhead .wordmark .dot { width: 18px; height: 18px; }
  .letter { position: absolute; left: 33px; top: 120px; width: 268px; font-size: 5.6px; line-height: 1.45; color: var(--ink-soft); }
  .letter__date, .letter__greeting { font-size: 7px; color: var(--ink); margin-bottom: 6px; }
  .letter p { margin-bottom: 7px; text-align: justify; }
  .letter__signoff { font-size: 9px; color: var(--ink); margin-top: 10px; }
  .letter__role { font-size: 5.6px; }
  .letterhead .contact { left: 33px; top: 414px; font-size: 5.6px; line-height: 1.4; }
  .letterhead .colour-bar { left: 0; right: 0; top: 454px; height: 4px; }
  .letterhead .colour-bar span { width: 16%; }

  /* Presentation folder */
  .folder { left: 371px; top: 34px; width: 336px; height: 475px; background: var(--black); }
  .folder .wordmark { position: absolute; left: 26px; top: 424px; font-size: 13px; }
  .folder .wordmark .dot { width: 18px; height: 18px; }

  /* DL envelopes (back view) */
  .envelope-back { position: absolute; background: var(--paper); box-shadow: 0 1px 3px rgba(0,0,0,.14); overflow: hidden; }
  .envelope-back svg { position: absolute; left: 0; top: 0; display: block; }
  .envelope--black { left: 732px; top: 86px; width: 444px; height: 192px; }
  .envelope--green { left: 732px; top: 296px; width: 444px; height: 192px; }
  .envelope--blue { left: 695px; top: 421px; width: 446px; height: 194px; }
  .envelope--red { left: 539px; top: 519px; width: 458px; height: 199px; }

  /* Envelope front */
  .envelope-front { left: 570px; top: 602px; width: 550px; height: 240px; }
  .envelope-front .wordmark { position: absolute; left: 37px; top: 50px; font-size: 15px; }
  .envelope-front .wordmark .dot { width: 22px; height: 22px; }
  .envelope-front__address { position: absolute; left: 69px; top: 72px; font-size: 8px; color: var(--ink-soft); }
  .envelope-front .colour-bar { left: 0; right: 0; top: 221px; height: 6px; }
  .envelope-front .colour-bar span { width: 16%; }

  /* Compliments slip */
  .comp-slip { left: 20px; top: 603px; width: 505px; height: 235px; }
  .comp-slip .wordmark { position: absolute; left: 27px; top: 38px; font-size: 16px; }
  .comp-slip .wordmark .dot { width: 24px; height: 24px; }
  .comp-slip__title { position: absolute; right: 26px; top: 43px; font-size: 15px; font-style: italic; color: var(--ink); }
  .comp-slip .contact { left: 26px; top: 175px; font-size: 7px; line-height: 1.4; }
  .comp-slip .colour-bar { left: 0; right: 0; top: 219px; height: 6px; }
  .comp-slip .colour-bar span { width: 16%; }
</style>
</head>
<body>

  <section class="sheet letterhead" aria-label="Letterhead">
    <div class="wordmark"><span class="dot"></span>brightkeyhomes</div>
    <div class="letter">
      <div class="letter__date">Jan/01/2015</div>
      <div class="letter__greeting">Dear Peter,</div>
      <p>Thank you for choosing our team to look after your home. We have reviewed the rental market in your area and believe the property is well placed for a strong return this season. Our property managers will inspect the home, prepare a full condition report and arrange any small repairs before the first open inspection. You will receive a written summary each month along with a clear statement of all income and costs.</p>
      <p>Our local knowledge of the coast and the suburbs means we can match the right tenants to the right homes. Every application is checked carefully, and we keep you informed at each step so there are no surprises. If you would like to discuss a sale in the future, our sales team is happy to provide a free appraisal at a time that suits you.</p>
      <p>Please call our office or reply by email should you have any questions about the agreement. We look forward to working with you and caring for your property over the years ahead.</p>
      <div class="letter__signoff">Marcus Hale</div>
      <div class="letter__role">Company Director</div>
    </div>
    <div class="contact">
      <div class="contact__col">Shop 4, 52 harbour parade<br>tidewater qld 4580<br><span class="label">Abn:</span> 62 418 207 553</div>
      <div class="contact__col">po box 2760<br>seagrove qld 4560</div>
      <div class="contact__col"><span class="label">P:</span>(07) 5000 2147<br><span class="label">F:</span>(07) 5000 2148<br><span class="label">E:</span>enquiry@brightkeyhomes.com.au<br>www.brightkeyhomes.com.au</div>
    </div>
    <div class="colour-bar"><span></span><span></span><span></span><span></span><span></span><span></span></div>
  </section>

  <section class="sheet folder" aria-label="Presentation folder">
    <div class="wordmark wordmark--light"><span class="dot"></span>brightkeyhomes</div>
  </section>

  <section class="envelope-back envelope--black" aria-label="Envelope with black flap">
    <svg width="444" height="80" viewBox="0 0 444 80">
      <path d="M0 0H444V4C430 28 300 58 222 66C144 58 14 28 0 4Z" fill="var(--black)"/>
      <circle cx="222" cy="33" r="14" fill="var(--red)"/>
    </svg>
  </section>

  <section class="envelope-back envelope--green" aria-label="Envelope with green flap">
    <svg width="444" height="80" viewBox="0 0 444 80">
      <path d="M0 0H444V4C430 28 300 56 222 64C144 56 14 28 0 4Z" fill="var(--flap-green)"/>
      <circle cx="222" cy="33" r="15" fill="#ffffff"/>
    </svg>
  </section>

  <section class="envelope-back envelope--blue" aria-label="Envelope with blue flap">
    <svg width="446" height="80" viewBox="0 0 446 80">
      <path d="M0 0H446V4C432 28 302 56 223 64C144 56 14 28 0 4Z" fill="var(--flap-blue)"/>
      <circle cx="223" cy="34" r="15" fill="#ffffff"/>
    </svg>
  </section>

  <section class="envelope-back envelope--red" aria-label="Envelope with red flap">
    <svg width="458" height="80" viewBox="0 0 458 80">
      <path d="M0 0H458V4C444 28 310 56 229 64C148 56 14 28 0 4Z" fill="var(--flap-red)"/>
      <circle cx="229" cy="34" r="15" fill="#ffffff"/>
    </svg>
  </section>

  <section class="sheet envelope-front" aria-label="Envelope front">
    <div class="wordmark"><span class="dot"></span>brightkeyhomes</div>
    <div class="envelope-front__address">Shop 4, 52 harbour parade, tidewater qld 4580</div>
    <div class="colour-bar"><span></span><span></span><span></span><span></span><span></span><span></span></div>
  </section>

  <section class="sheet comp-slip" aria-label="Compliments slip">
    <div class="wordmark"><span class="dot"></span>brightkeyhomes</div>
    <div class="comp-slip__title">With Compliments</div>
    <div class="contact">
      <div class="contact__col">Shop 4, 52 harbour parade<br>tidewater qld 4580<br><span class="label">Abn:</span> 62 418 207 553</div>
      <div class="contact__col">po box 2760<br>seagrove qld 4560</div>
      <div class="contact__col"><span class="label">P:</span>(07) 5000 2147<br><span class="label">F:</span>(07) 5000 2148<br><span class="label">E:</span>enquiry@brightkeyhomes.com.au<br>www.brightkeyhomes.com.au</div>
    </div>
    <div class="colour-bar"><span></span><span></span><span></span><span></span><span></span><span></span></div>
  </section>

</body>
</html>
```